Brightwave Reach - Business Card

We need a business card for a Social Media Marketing company that specializes in online marketing for small businesses in Canada using common Social Media platforms such as Pixlora, Chatterly, Blinkpost & Quibber.

I have uploaded a copy of our logo which I would like utilized in the business card. We would like the business card to be modern yet classy design.

Our website is www.brightwavereach.ca

Industry/Entity Type

Marketing

Contact Information for Business Card

Email: info@brightwavereach.ca
Website: www.brightwavereach.ca
Telephone: 604-555-0193

Colors

Designer to choose colors to be used in the design.

Requirements
Must have
• Social Media icons on reverse
• Please add some designs with color.

```html
<!DOCTYPE html>
<html lang="en">
<head>
<meta charset="utf-8">
<title>Brightwave Reach – Business Card</title>
<link rel="stylesheet" href="https://fonts.googleapis.com/css2?family=Open+Sans:wght@400;700&display=swap">
<style>
  :root {
    --backdrop: #e6e4e1;
    --card: #3a3f42;
    --ink: #ffffff;
    --ink-soft: #e4e6e7;
    --accent: #ffffff;
    --pop-1: #f2a93b;
    --pop-2: #3bb3c9;
    --pop-3: #e8594f;
    --pop-4: #7cc167;
  }
  * { box-sizing: border-box; margin: 0; padding: 0; }
  html, body {
    width: 1200px;
    height: 844px;
    overflow: hidden;
    background: var(--backdrop);
    font-family: "Open Sans", Arial, sans-serif;
  }
  .stage {
    position: relative;
    width: 1200px;
    height: 844px;
  }
  .card {
    position: absolute;
    top: 273px;
    width: 520px;
    height: 298px;
    background: var(--card);
    overflow: hidden;
    box-shadow: 0 6px 18px rgba(0,0,0,0.18);
  }
  .card--back { left: 50px; }
  .card--front { left: 630px; }

  /* contact side */
  .band {
    position: absolute;
    left: 0;
    right: 0;
    height: 16px;
    background: var(--accent);
  }
  .band--top { top: 12px; }
  .band--bottom { bottom: 12px; }

  .identity {
    position: absolute;
    top: 74px;
    left: 0;
    right: 0;
    text-align: center;
    color: var(--ink);
  }
  .identity__name {
    display: inline-block;
    font-weight: 700;
    font-size: 17px;
    letter-spacing: 0.3px;
    text-transform: uppercase;
    padding: 0 6px 2px;
    border-bottom: 1px solid var(--ink-soft);
  }
  .identity__title {
    font-size: 13px;
    margin-top: 3px;
    color: var(--ink-soft);
  }
  .contact {
    position: absolute;
    top: 158px;
    left: 0;
    right: 0;
    text-align: center;
    color: var(--ink);
    font-size: 14px;
    line-height: 19px;
    list-style: none;
  }
  .social {
    position: absolute;
    top: 232px;
    left: 0;
    right: 0;
    display: flex;
    justify-content: center;
    gap: 18px;
    list-style: none;
    color: var(--ink);
    font-size: 11px;
    line-height: 14px;
  }
  .social__item {
    display: flex;
    align-items: center;
    gap: 5px;
  }
  .social__dot {
    width: 9px;
    height: 9px;
    border-radius: 50%;
    flex: none;
  }
  .social__dot--pixlora { background: var(--pop-1); }
  .social__dot--chatterly { background: var(--pop-2); }
  .social__dot--blinkpost { background: var(--pop-3); }
  .social__dot--quibber { background: var(--pop-4); }

  /* brand side */
  .tab {
    position: absolute;
    width: 22px;
    height: 40px;
    background: var(--accent);
  }
  .tab--right { right: 0; top: 30px; }
  .tab--left { left: 0; top: 196px; }

  .brand {
    position: absolute;
    top: 50%;
    left: 50%;
    transform: translate(-50%, -50%);
    display: flex;
    align-items: center;
    gap: 14px;
    color: var(--ink);
  }
  .brand__square {
    width: 26px;
    height: 26px;
    background: var(--pop-1);
    flex: none;
  }
  .brand__name {
    font-weight: 700;
    font-size: 34px;
    line-height: 38px;
    text-transform: uppercase;
    letter-spacing: 0.5px;
    white-space: nowrap;
  }
</style>
</head>
<body>
  <main class="stage">
    <section class="card card--back" aria-label="Business card, contact side">
      <div class="band band--top"></div>
      <div class="band band--bottom"></div>
      <div class="identity">
        <div class="identity__name">Marcus Hale</div>
        <div class="identity__title">Managing Director</div>
      </div>
      <ul class="contact">
        <li>604-555-0193</li>
        <li>info@brightwavereach.ca</li>
        <li>www.brightwavereach.ca</li>
      </ul>
      <ul class="social" aria-label="Social media">
        <li class="social__item"><span class="social__dot social__dot--pixlora"></span>Pixlora</li>
        <li class="social__item"><span class="social__dot social__dot--chatterly"></span>Chatterly</li>
        <li class="social__item"><span class="social__dot social__dot--blinkpost"></span>Blinkpost</li>
        <li class="social__item"><span class="social__dot social__dot--quibber"></span>Quibber</li>
      </ul>
    </section>

    <section class="card card--front" aria-label="Business card, brand side">
      <div class="tab tab--right"></div>
      <div class="tab tab--left"></div>
      <div class="brand">
        <span class="brand__square"></span>
        <span class="brand__name">Brightwave<br>Reach</span>
      </div>
    </section>
  </main>
</body>
</html>
```